Simple landing page for Brambles cookbook

I need a one page landingpage where customers can order the cookbook.
This is a cookbook of a collection of recipes from our deli that we used to run.
I need a landing page where customers can come and order the book. I also need it coded. I already have the domain through hostwell.
I can send the file of the book through wetransfer. It's too big to upload here. Just so you get the feel that I am looking for.
I attached a simple text as an introduction to the page. But I am open to any suggestions. I want it all to be about the experience that we are sharing the recipes with everybody and that it's for sale. The book is $29.99, shipping included.
Customers have to be able to click and buy the book from it.

Coding

Coded - Design and coding required

Number of Pages Required

1 page

Font styles to use
Sans Serif

Requirements
Must have
• Same colors as the cookbook

```html
<!DOCTYPE html>
<html lang="en">
<head>
<meta charset="utf-8">
<title>Brambles – The Cookbook</title>
<link href="https://fonts.googleapis.com/css2?family=Open+Sans:wght@400;600;700&family=Work+Sans:wght@800&display=swap" rel="stylesheet">
<style>
  :root {
    --brand-pink: #d4145a;
    --ink: #1a1a1a;
    --body-text: #555555;
    --footer-bg: #181818;
    --white: #ffffff;
  }
  * { box-sizing: border-box; margin: 0; padding: 0; }
  html, body { width: 894px; height: 1200px; overflow: hidden; }
  body { font-family: "Open Sans", sans-serif; background: var(--white); position: relative; color: var(--ink); }

  .hero {
    position: absolute; left: 0; top: 0; width: 894px; height: 480px;
    background:
      radial-gradient(ellipse 260px 230px at 190px 260px, #c8894a 0%, #8a4a2a 55%, transparent 80%),
      radial-gradient(ellipse 320px 160px at 620px 330px, #c9a15a 0%, #7a5530 60%, transparent 90%),
      linear-gradient(180deg, #1f2230 0%, #3a2a26 45%, #5a3b24 100%);
  }
  .site-header { position: absolute; left: 0; top: 0; width: 894px; height: 60px; }
  .brand { position: absolute; left: 83px; top: 8px; font-weight: 700; font-size: 32px; color: var(--white); letter-spacing: 1px; }
  .main-nav { position: absolute; left: 291px; top: 20px; display: flex; gap: 24px; }
  .main-nav a { color: var(--white); text-decoration: none; font-weight: 700; font-size: 12px; position: relative; }
  .main-nav a.active::before { content: ""; position: absolute; left: 0; right: 0; top: -20px; height: 3px; background: var(--white); }
  .phone { position: absolute; left: 657px; top: 12px; display: flex; align-items: center; gap: 16px; color: var(--white); font-weight: 700; font-size: 13px; }
  .phone-icon { width: 33px; height: 33px; border: 2px solid var(--white); border-radius: 50%; display: flex; align-items: center; justify-content: center; }

  .hero-copy { position: absolute; left: 445px; top: 160px; width: 340px; color: var(--white); }
  .hero-copy h1 { font-family: "Work Sans", sans-serif; font-weight: 800; font-size: 36px; line-height: 1; }
  .hero-copy p { margin-top: 20px; font-size: 13.5px; font-weight: 600; line-height: 20px; }

  .side-social { position: absolute; left: 835px; top: 162px; display: flex; flex-direction: column; align-items: center; gap: 10px; }
  .side-social span { display: block; width: 8px; height: 8px; border-radius: 50%; background: var(--white); }
  .side-social span.ring { width: 28px; height: 28px; background: transparent; border: 1.5px solid var(--white); }

  .hero-wave { position: absolute; left: 0; top: 360px; }
  .scroll-down { position: absolute; left: 415px; top: 396px; width: 64px; height: 64px; border-radius: 50%; background: var(--white); box-shadow: 0 3px 10px rgba(0,0,0,.2); display: flex; align-items: center; justify-content: center; }

  .welcome { position: absolute; left: 83px; top: 530px; width: 440px; }
  .welcome h2 { font-family: "Work Sans", sans-serif; font-weight: 800; font-size: 28px; line-height: 1; color: var(--ink); }
  .price { margin-top: 12px; font-size: 20px; color: var(--brand-pink); font-weight: 400; }
  .welcome p.body { margin-top: 18px; font-size: 10.8px; line-height: 18.5px; color: var(--body-text); text-align: justify; }
  .welcome p.body + p.body { margin-top: 13px; }
  .buy-button { display: inline-block; margin-top: 28px; width: 115px; height: 37px; line-height: 37px; text-align: center; background: var(--brand-pink); color: var(--white); font-weight: 700; font-size: 11px; border-radius: 3px; text-decoration: none; }

  .book-cover {
    position: absolute; left: 577px; top: 526px; width: 235px; height: 354px;
    background: linear-gradient(160deg, #e6f1f8 0%, #f4f6f8 35%, #d9a05a 60%, #e9ecef 100%);
    box-shadow: 6px 8px 18px rgba(0,0,0,.25);
    border-right: 10px solid #e4e4e4;
  }

  .site-footer { position: absolute; left: 0; top: 930px; width: 894px; height: 270px; }
  .footer-brand { position: absolute; left: 0; width: 894px; top: 113px; text-align: center; font-weight: 700; font-size: 36px; color: var(--white); letter-spacing: 1px; }
  .footer-nav { position: absolute; left: 0; width: 894px; top: 174px; display: flex; justify-content: center; align-items: center; gap: 25px; color: var(--white); font-weight: 700; font-size: 15px; }
  .footer-nav a { color: var(--white); text-decoration: none; }
  .footer-rule { position: absolute; left: 83px; width: 728px; top: 221px; border-top: 1px solid #777; }
  .copyright { position: absolute; left: 0; width: 894px; top: 234px; text-align: center; color: var(--white); font-size: 11px; }
  .footer-social { position: absolute; left: 684px; top: 229px; display: flex; gap: 4px; }
  .footer-social span { width: 29px; height: 29px; border-radius: 50%; border: 1.5px solid var(--white); }
  .footer-social span.filled { background: var(--brand-pink); border-color: var(--brand-pink); }
</style>
</head>
<body>

<section class="hero">
  <div class="hero-photo" role="img" aria-label="Close-up photograph of a sesame burger with fries and dipping sauce" style="position:absolute;inset:0;"></div>

  <header class="site-header">
    <div class="brand">BRAMBLES</div>
    <nav class="main-nav">
      <a class="active" href="#">HOME</a>
      <a href="#">ABOUT</a>
      <a href="#">BUY THE BOOK</a>
      <a href="#">CONTACT</a>
    </nav>
    <div class="phone">
      <span class="phone-icon">
        <svg width="13" height="13" viewBox="0 0 24 24" fill="#fff"><path d="M6.6 10.8a15.1 15.1 0 0 0 6.6 6.6l2.2-2.2c.3-.3.7-.4 1-.2 1.1.4 2.3.6 3.6.6.6 0 1 .4 1 1V20c0 .6-.4 1-1 1A17 17 0 0 1 3 4c0-.6.4-1 1-1h3.5c.6 0 1 .4 1 1 0 1.3.2 2.5.6 3.6.1.3 0 .7-.2 1z"/></svg>
      </span>
      <span>+1 (555) 010 0199</span>
    </div>
  </header>

  <div class="hero-copy">
    <h1>BRAMBLES</h1>
    <p>Brambles started out as a deli but eventually morphed into the sandwich shop we all know it as today.</p>
  </div>

  <div class="side-social" aria-label="Social links">
    <span class="ring"></span><span></span><span></span><span></span>
  </div>

  <svg class="hero-wave" width="894" height="120" viewBox="0 360 894 120">
    <path d="M0 402 C80 445 150 468 224 462 C400 448 520 392 670 386 C760 382 840 415 894 450 L894 480 L0 480 Z" fill="#d4145a"/>
    <path d="M0 410 C80 455 150 478 224 472 C400 458 520 402 670 396 C760 392 840 425 894 458 L894 480 L0 480 Z" fill="#ffffff"/>
    <path d="M398 430 A50 50 0 0 1 496 430" fill="none" stroke="#ffffff" stroke-width="1.2"/>
  </svg>
  <div class="scroll-down">
    <svg width="22" height="22" viewBox="0 0 24 24" fill="#333"><path d="M9 3h6v9h5l-8 9-8-9h5z"/></svg>
  </div>
</section>

<main class="welcome">
  <h2>WELCOME TO BRAMBLES</h2>
  <div class="price">The book is $29.99</div>
  <p class="body">Opening it’s doors in January of 2010, Brambles European Deli was a sandwich shop in Harrowfield, Eastmoor, but also a lot more than that. We spent five years with this business until it’s eventual closure in April of 2015. It was a special time where we met tons of amazing people, who we loved to see and serve. Brambles started out as a deli but eventually morphed into the sandwich shop we all know it as today.</p>
  <p class="body">We are overwhelmed with the continuous positive messages and comments we get on our Gatherly page that is still up and running. Unfortunately, we can’t open another Brambles, but we can offer you this collection of our recipes for you to try out at home with your family and friends. We truly hope you will enjoy making these sandwiches just as much as we did. If you do, please post your pictures of you making a meal or the finished product, or even enjoying it!</p>
  <a class="buy-button" href="#">BUY THE BOOK</a>
</main>

<div class="book-cover" role="img" aria-label="Cover of the Brambles sandwiches cookbook with a photo of a stacked sandwich, 28 recipes"></div>

<footer class="site-footer">
  <svg width="894" height="270" viewBox="0 0 894 270" style="position:absolute;left:0;top:0;">
    <path d="M0 35 C90 85 170 100 260 95 C420 85 540 15 670 12 C770 10 840 40 894 70 L894 270 L0 270 Z" fill="#181818"/>
    <path d="M0 50 C90 98 170 112 260 107 C420 98 540 28 670 25 C770 23 840 55 894 92 L894 102 C840 68 770 36 670 38 C540 42 420 110 260 118 C170 123 90 110 0 60 Z" fill="#d4145a"/>
  </svg>
  <div class="footer-brand">BRAMBLES</div>
  <nav class="footer-nav">
    <a href="#">HOME</a><span>|</span>
    <a href="#">ABOUT</a><span>|</span>
    <a href="#">BUY THE BOOK</a><span>|</span>
    <a href="#">CONTACT</a>
  </nav>
  <div class="footer-rule"></div>
  <div class="copyright">©&nbsp; 2022 BRAMBLES &nbsp;|&nbsp; All Rights Reserved</div>
  <div class="footer-social" aria-label="Social links">
    <span class="filled"></span><span></span><span></span><span></span>
  </div>
</footer>

</body>
</html>
```